Local Flower Farm Needs Business Card Design

I need business cards designed for a flower farm based in Eudora, Kansas.
Business Info:
We are a local cut flower farm located in Eudora, Kansas, founded by Corinne Haldwick. What started as a passion for agriculture and search for more joy in daily life has blossomed into a small business dedicated to providing the community with beautiful, fresh, and sustainable flowers. We specialize in local, seasonal blooms, ensuring that every petal reflects the care and dedication we pour into our craft. Our mission is to deliver the highest quality flowers directly to our customers through local farmers markets and to florists who share our commitment to sustainability. Join us in celebrating the beauty of nature, one bloom at a time!
Contact Details:
Corinne Haldwick
Owner
Phone 913-555-0147
Facebook: Rosalind Thorpe Gardens
Instagram: @RosalindThorpeGardens
Website: RosalindThorpeGardens.example
Target Market(s)
Wholesale to Florists and Direct to Consumer via Farmers Market
Industry/Entity Type
Florist, Farm
Contact Information for Business Card
Name, Contact Info, Logo
Look and feel
Each slider illustrates characteristics of the customer's brand and the style your logo design should communicate.

```html
<!DOCTYPE html>
<html lang="en">
<head>
<meta charset="utf-8">
<title>Rosalind Thorpe Gardens – Business Card</title>
<link href="https://fonts.googleapis.com/css2?family=Cormorant+Garamond:wght@600&family=Quicksand:wght@500&display=swap" rel="stylesheet">
<style>
  :root {
    --backdrop: #e6e6e3;
    --card-light: #ffffff;
    --card-dark: #0d2828;
    --ink-dark: #123030;
    --ink-light: #f4f4f1;
    --icon-green: #3f5a22;
    --rule: #2a2a2a;
    --muted: #3a3a3a;
  }
  * { box-sizing: border-box; margin: 0; padding: 0; }
  html, body { width: 1200px; height: 900px; overflow: hidden; }
  body {
    background: var(--backdrop);
    position: relative;
    font-family: "Quicksand", sans-serif;
  }
  .card {
    position: absolute;
    left: 250px;
    width: 700px;
    height: 400px;
    border-radius: 26px;
    box-shadow: 0 10px 30px rgba(0,0,0,0.18);
    overflow: hidden;
  }
  .card--front { top: 40px; background: var(--card-light); }
  .card--back { top: 460px; background: var(--card-dark); }

  .brand-seal {
    position: absolute;
    border-radius: 50%;
    display: flex;
    align-items: center;
    justify-content: center;
    text-align: center;
    font-family: "Cormorant Garamond", serif;
    font-weight: 600;
    letter-spacing: 0.12em;
    text-transform: uppercase;
  }
  .card--front .brand-seal {
    left: 50px; top: 28px;
    width: 170px; height: 170px;
    border: 1.5px solid var(--ink-dark);
    color: var(--ink-dark);
    font-size: 19px;
    line-height: 1.25;
  }
  .card--back .brand-seal {
    left: 225px; top: 75px;
    width: 250px; height: 250px;
    border: 1.5px solid var(--ink-light);
    color: var(--ink-light);
    font-size: 28px;
    line-height: 1.25;
  }

  .holder {
    position: absolute;
    right: 48px; top: 62px;
    text-align: right;
  }
  .holder__name {
    font-family: "Cormorant Garamond", serif;
    font-weight: 600;
    font-size: 27px;
    letter-spacing: 0.04em;
    text-transform: uppercase;
    color: #111;
  }
  .holder__role { font-size: 14px; color: var(--muted); margin-top: 2px; }

  .rule { position: absolute; height: 1px; background: var(--rule); }
  .rule--upper { left: 48px; right: 250px; top: 222px; }
  .rule--lower { left: 360px; right: 48px; top: 318px; }

  .contact-list {
    position: absolute;
    list-style: none;
    font-size: 16px;
    color: #1c1c1c;
  }
  .contact-list--main { left: 48px; top: 236px; }
  .contact-list--social { left: 380px; top: 332px; font-size: 15px; }
  .contact-list li {
    display: flex; align-items: center; gap: 10px; height: 25px;
  }
  .icon {
    width: 18px; height: 18px; border-radius: 3px;
    background: var(--icon-green);
    flex: none;
    display: flex; align-items: center; justify-content: center;
  }
  .icon svg { width: 12px; height: 12px; }
  .icon--plain { background: var(--icon-green); }
</style>
</head>
<body>
  <section class="card card--front">
    <div class="brand-seal">Rosalind<br>Thorpe<br>Gardens</div>

    <div class="holder">
      <p class="holder__name">Corinne Haldwick</p>
      <p class="holder__role">Owner</p>
    </div>

    <div class="rule rule--upper"></div>

    <ul class="contact-list contact-list--main">
      <li><span class="icon"><svg viewBox="0 0 12 12"><path d="M3 1.5l1.6 2.2-.9 1.1c.6 1.2 1.5 2.1 2.6 2.6l1.1-.9 2.2 1.6-.8 1.6C6 9.6 2.4 6 1.7 2.3z" fill="#fff"/></svg></span>913-555-0147</li>
      <li><span class="icon"><svg viewBox="0 0 12 12"><rect x="1" y="2.5" width="10" height="7" fill="none" stroke="#fff" stroke-width="1.2"/><path d="M1 2.5l5 4 5-4" fill="none" stroke="#fff" stroke-width="1.2"/></svg></span>RosalindThorpe@Gardens.example</li>
      <li><span class="icon"><svg viewBox="0 0 12 12"><circle cx="6" cy="6" r="4.8" fill="none" stroke="#fff" stroke-width="1.1"/><ellipse cx="6" cy="6" rx="2" ry="4.8" fill="none" stroke="#fff" stroke-width="1"/><path d="M1.2 6h9.6" stroke="#fff" stroke-width="1"/></svg></span>www.RosalindThorpeGardens.example</li>
    </ul>

    <div class="rule rule--lower"></div>

    <ul class="contact-list contact-list--social">
      <li><span class="icon icon--plain"></span>Rosalind Thorpe Gardens</li>
      <li><span class="icon icon--plain"></span>@RosalindThorpeGardens</li>
    </ul>
  </section>

  <section class="card card--back">
    <div class="brand-seal">Rosalind<br>Thorpe<br>Gardens</div>
  </section>
</body>
</html>
```